A website for a Maltese Law Firm

Our law firm needs a website to further its business. The site should have a simple yet effective design. We would need the following sections: About us, Practice Areas, About Malta, Contact. These should be further split as follows:

About us: Our firm, Our values, What others say, Offices

Practice Areas: Crimimal, Citizenship & Residence, Sovereign Patron Pathway, Criminal Defence, Civil Litigation, Arbitration and ADR, Commercial and Corporate, Media Law.

About Malta: just one section.

Contact: Just one section

We would also need a news feed at the front of the site to include latest news regarding our cases.

At the bottom we need a section for our Terms and a Privacy Statement.

Our logo is being attached.

Target Market(s)

All clients looking for legal assistance in Malta

Industry/Entity Type

Legal

Coding

Coded - Design and coding required

Number of Pages Required

1 page

Requirements
Must have
• It must be simple yet striking.

```html
<!DOCTYPE html>
<html lang="en">
<head>
<meta charset="utf-8">
<title>Harbourline Legal</title>
<link rel="stylesheet" href="https://fonts.googleapis.com/css2?family=Cinzel:wght@400;700&family=Raleway:ital,wght@0,400;0,500;0,600;1,400&family=Open+Sans:wght@400;600&display=swap">
<style>
:root{
  --ink:#222;
  --text:#555;
  --muted:#888;
  --white:#fff;
  --news:#3a3632;
  --footer:#141414;
  --footer-bar:#0c0c0c;
  --footer-text:#9a9a9a;
}
*{margin:0;padding:0;box-sizing:border-box}
html,body{width:674px;height:1200px;overflow:hidden;background:var(--white)}
body{position:relative;font-family:'Open Sans',sans-serif;color:var(--text)}

/* header */
.site-header{position:absolute;left:0;top:0;width:674px;height:59px;background:var(--white);border-bottom:1px solid #ddd}
.brand{position:absolute;left:106px;top:20px;display:flex;align-items:center;gap:7px}
.brand-mark{width:12px;height:12px;background:var(--ink)}
.brand-name{font-family:'Raleway',sans-serif;font-size:15px;font-weight:600;color:var(--ink);line-height:18px;white-space:nowrap}
.main-nav{position:absolute;top:25px;left:308px;display:flex;gap:13px;font-family:'Raleway',sans-serif;font-size:9px;color:var(--text)}
.main-nav .active{color:var(--ink);position:relative}
.main-nav .active::after{content:"";position:absolute;left:-3px;right:-3px;top:19px;height:2px;background:var(--ink)}

/* hero */
.hero{position:absolute;left:0;top:59px;width:674px;height:298px;background:linear-gradient(180deg,#1a3a9c 0%,#2a4fb8 30%,#12266e 60%,#070f3a 100%);color:var(--white);text-align:center}
.hero-title{position:absolute;top:88px;left:0;right:0;font-family:'Cinzel',serif;font-weight:400;font-size:25px;letter-spacing:.5px}
.hero-sub{position:absolute;top:119px;left:0;right:0;font-family:'Cinzel',serif;font-size:13.5px}
.hero-rule{position:absolute;left:170px;width:352px;height:1px;background:rgba(255,255,255,.8)}
.hero-text{position:absolute;top:159px;left:160px;width:354px;font-family:'Raleway',sans-serif;font-style:italic;font-size:8px;line-height:10.5px}
.hero-dots{position:absolute;top:280px;left:318px;display:flex;gap:2px}
.hero-dots span{width:7px;height:7px;border-radius:50%;background:var(--white);border:1px solid var(--white)}
.hero-dots span:first-child{background:transparent}

/* about */
.about{position:absolute;left:0;top:357px;width:674px;height:213px}
.section-title{font-family:'Cinzel',serif;color:#555;font-weight:400}
.about h2{position:absolute;left:101px;top:42px;font-size:17px}
.about-lead{position:absolute;left:101px;top:71px;width:325px;font-size:6.6px;line-height:10px}
.about-body{position:absolute;left:101px;top:99px;width:325px;font-size:5.5px;line-height:10px}
.btn{position:absolute;border:1.5px solid #555;font-family:'Raleway',sans-serif;font-size:7px;color:#444;text-align:center;background:transparent}
.about .btn{left:102px;top:149px;width:74px;height:21px;line-height:18px}
.about-photo{position:absolute;left:440px;top:42px;width:130px;height:121px;background:linear-gradient(135deg,#3a3f4a,#6b5a4c 55%,#2e3442);border:1px solid #999}
.about-photo::after{content:"";position:absolute;inset:5px;border:1px solid rgba(255,255,255,.85)}

/* practice */
.practice{position:absolute;left:0;top:570px;width:674px;height:236px;background:linear-gradient(180deg,#dcdcdc,#ececec 50%,#e0e0e0)}
.practice h2{position:absolute;top:25px;left:0;right:0;text-align:center;font-size:15px}
.area{position:absolute;width:230px;height:44px}
.area-icon{position:absolute;left:0;top:0;width:42px;height:42px;border:1.5px solid #222;border-radius:50%;background:var(--white);display:flex;align-items:center;justify-content:center}
.area-line{position:absolute;left:50px;top:2px;width:1px;height:38px;background:#999}
.area h3{position:absolute;left:58px;top:4px;font-family:'Raleway',sans-serif;font-size:9.5px;font-weight:500;color:var(--ink);white-space:nowrap}
.area p{position:absolute;left:58px;top:18px;width:175px;font-size:6.6px;line-height:12px;color:var(--muted)}
.practice .btn{left:301px;top:195px;width:68px;height:18px;line-height:15px;font-size:6.8px}

/* news */
.news{position:absolute;left:0;top:806px;width:674px;height:231px;background:linear-gradient(90deg,#2c2f3a,#4a4038 45%,#2f2b2a)}
.news h2{position:absolute;top:30px;left:0;right:0;text-align:center;font-size:14.5px;color:var(--white)}
.news h2 svg{vertical-align:middle;margin:0 6px}
.card{position:absolute;top:64px;width:146px;text-align:center;color:var(--white)}
.card-img{height:78px;background:linear-gradient(135deg,#c8cdd3,#6e6a66 60%,#3d3a38)}
.card h3{font-family:'Raleway',sans-serif;font-weight:500;font-size:8.5px;margin-top:7px}
.card p{font-size:6.5px;line-height:10.5px;margin-top:3px;color:#e8e8e8}

/* footer */
.site-footer{position:absolute;left:0;top:1037px;width:674px;height:130px;background:var(--footer)}
.f-col{position:absolute;top:25px}
.f-col h4{font-family:'Cinzel',serif;font-weight:400;font-size:8.5px;color:var(--white);letter-spacing:.5px;margin-bottom:7px;white-space:nowrap}
.f-col li{list-style:none;font-size:6px;line-height:12.3px;color:var(--footer-text);white-space:nowrap}
.f-divider{position:absolute;top:25px;width:1px;height:85px;background:#333}
.f-terms p{width:165px;font-size:6px;line-height:11.5px;color:var(--footer-text)}
.f-contact .phone{font-size:7.5px;color:#bbb;display:flex;align-items:center;gap:5px}
.f-contact .mail{display:flex;align-items:center;gap:5px}
.social{display:flex;gap:2px;margin-top:6px}
.social span{width:13px;height:13px;border:1px solid #bbb;border-radius:50%}
.footer-bar{position:absolute;left:0;top:1167px;width:674px;height:33px;background:var(--footer-bar);text-align:center;font-size:6px;color:#aaa;line-height:33px}
</style>
</head>
<body>

<header class="site-header">
  <div class="brand">
    <span class="brand-mark"></span>
    <span class="brand-name">Harbourline Legal</span>
  </div>
  <nav class="main-nav">
    <span class="active">Home</span><span>About us</span><span>Practice Areas</span><span>About Malta</span><span>Contact us</span>
  </nav>
</header>

<section class="hero" role="img" aria-label="Night skyline of a harbour city with lit towers over the water">
  <h1 class="hero-title">Citizenship &amp; Residence Law</h1>
  <div class="hero-sub">Dis Parturient Montes Nascetur</div>
  <div class="hero-rule" style="top:149px"></div>
  <p class="hero-text">In massa libero interdum nec interdum vel blandit sed nulla in ullamcorper est eget tempor cursus neque mi consectetuer mi a ultricies massa est sed</p>
  <div class="hero-rule" style="top:195px"></div>
  <div class="hero-dots"><span></span><span></span><span></span><span></span></div>
</section>

<section class="about">
  <h2 class="section-title">About Malta</h2>
  <p class="about-lead">Curabitur iaculis tempus eros Curabitur vel mi sit amet magna malesuada ultrices Ut nisi erat fermentum vel congue id euismod in elit Fusce ultricies orci ac feugiat suscipit leo massa sodales</p>
  <p class="about-body">commodo a mi Morbi ornare gravida elit Integer congue augue et malesuada iaculis ipsum dui aliquet felis at cursus magna nisl nec elit Praesent elementum elit at tellus nec ultricies sit amet porttitor mattis enim In massa libero interdum nec interdum vel blandit sed nulla In ullamcorper est eget tempor cursus neque mi consectetuer mi a ultricies massa est sed nisl Class aptent taciti sociosqu ad litora torquent per conubia nostra per inceptos hymenaeos</p>
  <span class="btn">READ MORE</span>
  <div class="about-photo" role="img" aria-label="Portrait of a lawyer in a suit in front of bookshelves"></div>
</section>

<section class="practice">
  <h2 class="section-title">Practice Areas</h2>

  <div class="area" style="left:99px;top:62px">
    <div class="area-icon"><svg width="22" height="22" viewBox="0 0 22 22"><path d="M2 11 L9 4 L14 9 V20 H2 Z" fill="#111"/><rect x="11" y="12" width="9" height="8" fill="#111"/><rect x="4" y="13" width="3" height="3" fill="#fff"/><rect x="14" y="15" width="3" height="3" fill="#fff"/></svg></div>
    <div class="area-line"></div>
    <h3>Citizenship &amp; Residence</h3>
    <p>Du venenatis in tristique eu imperdiet ac nisl Cum sociis natoque penatibus et magnis dis</p>
  </div>

  <div class="area" style="left:349px;top:62px">
    <div class="area-icon"><svg width="22" height="22" viewBox="0 0 22 22" fill="none" stroke="#111" stroke-width="1.2"><path d="M3 5 H10 L13 8 H19"/><circle cx="12" cy="15" r="5"/><text x="12" y="17.5" font-size="7" text-anchor="middle" fill="#111" stroke="none" font-family="Open Sans,sans-serif">$</text></svg></div>
    <div class="area-line"></div>
    <h3>Sovereign Patron Pathway</h3>
    <p>Du venenatis in tristique eu imperdiet ac nisl Cum sociis natoque penatibus et magnis dis</p>
  </div>

  <div class="area" style="left:102px;top:130px">
    <div class="area-icon"><svg width="24" height="16" viewBox="0 0 24 16" fill="none" stroke="#111" stroke-width="1.2"><path d="M2 3 H22 V7 H12 L10 13 H6 L8 7 H2 Z"/></svg></div>
    <div class="area-line"></div>
    <h3>Criminal Defence</h3>
    <p>Du venenatis in tristique eu imperdiet ac nisl Cum sociis natoque penatibus et magnis dis</p>
  </div>

  <div class="area" style="left:352px;top:130px">
    <div class="area-icon"><svg width="22" height="22" viewBox="0 0 22 22"><rect x="3" y="4" width="9" height="16" fill="#111"/><rect x="12" y="9" width="7" height="11" fill="#111"/><g fill="#fff"><rect x="5" y="7" width="2" height="2"/><rect x="8" y="7" width="2" height="2"/><rect x="5" y="11" width="2" height="2"/><rect x="8" y="11" width="2" height="2"/><rect x="14" y="12" width="2" height="2"/></g></svg></div>
    <div class="area-line"></div>
    <h3>Commercial and Corporate</h3>
    <p>Du venenatis in tristique eu imperdiet ac nisl Cum sociis natoque penatibus et magnis dis</p>
  </div>

  <span class="btn">VIEW ALL</span>
</section>

<section class="news">
  <h2 class="section-title"><svg width="16" height="8" viewBox="0 0 16 8"><path d="M0 4 H16 M10 0 L15 4 L10 8" stroke="#fff" fill="none"/></svg>Latest News<svg width="16" height="8" viewBox="0 0 16 8"><path d="M16 4 H0 M6 0 L1 4 L6 8" stroke="#fff" fill="none"/></svg></h2>
  <article class="card" style="left:106px">
    <div class="card-img" role="img" aria-label="Business people shaking hands in an office"></div>
    <h3>Atricies sit amet porttitor</h3>
    <p>mattis enim In massa libero interdum nec interdum vel blandit sed nulla In ullamcorper est eget tempor cursus neque</p>
  </article>
  <article class="card" style="left:266px">
    <div class="card-img" role="img" aria-label="Lawyer reading documents beside scales of justice"></div>
    <h3>Atricies sit amet porttitor</h3>
    <p>mattis enim In massa libero interdum nec interdum vel blandit sed nulla In ullamcorper est eget tempor cursus neque</p>
  </article>
  <article class="card" style="left:426px">
    <div class="card-img" role="img" aria-label="Two colleagues meeting with a client"></div>
    <h3>Atricies sit amet porttitor</h3>
    <p>mattis enim In massa libero interdum nec interdum vel blandit sed nulla In ullamcorper est eget tempor cursus neque</p>
  </article>
</section>

<footer class="site-footer">
  <div class="f-col" style="left:137px"><h4>Company</h4><ul><li>Home</li><li>About Us</li><li>Our Blogs</li><li>News</li></ul></div>
  <div class="f-divider" style="left:195px"></div>
  <div class="f-col" style="left:212px"><h4>Services</h4><ul><li>Practice Areas</li><li>About Malta</li><li>Support</li><li>Contact Us</li></ul></div>
  <div class="f-divider" style="left:274px"></div>
  <div class="f-col f-contact" style="left:295px"><h4>Contact Us</h4><ul>
    <li>12/4, Harbour Lane, Valletta</li>
    <li>88, Olive Grove Road, Birkirkara</li>
    <li class="phone"><svg width="8" height="8" viewBox="0 0 8 8"><path d="M1 1 L3 1 L3.5 3 L2.5 3.7 Q3.5 5.5 4.5 5.5 L5 4.5 L7 5 L7 7 Q2 7.5 1 1 Z" fill="none" stroke="#bbb" stroke-width=".8"/></svg>(356) 5550-0123</li>
    <li class="mail"><svg width="8" height="6" viewBox="0 0 8 6"><rect width="8" height="6" fill="#bbb"/><path d="M0 0 L4 3 L8 0" stroke="#141414" fill="none" stroke-width=".7"/></svg>info@harbourline.example</li>
  </ul>
  <div class="social"><span></span><span></span><span></span><span></span></div></div>
  <div class="f-divider" style="left:396px"></div>
  <div class="f-col f-terms" style="left:412px"><h4>Terms &amp; Privacy Statement</h4>
    <p>Du venenatis in tristique eu imperdiet ac nisl Cum sociis natoque penatibus et magnis dis parturient montes nascetur ridiculus mus In iaculis facilisis massa Etiam eu urna Sed porta Suspendisse quam leo molestie sed luctus quis feugiat in pede Fusce tellus</p>
  </div>
</footer>
<div class="footer-bar">© 2016 Company Name &nbsp;All right reserved &nbsp;Term of Use</div>

</body>
</html>
```